KVOR Individual and Corporate Development Business Card Design

KVOR needs a business card design that is aligned with it's values and targetted markets. Coherent Lattice of Adaptive Reasoning Method's self diagnosis model and tools, which can be used for personal improvement and team/business performance enhancement, is based on the learnings of over 20 years of medical practitioning. KVOR supercharges personal effectiveness and awareness to also increase team and business performance.

The targetted markets are high performance individuals and teams who aspire seek to enhance their capabilities and achieve their absolute best potential.

Look and feel for the business card design we are looking for is high technology, premium, fresh, new and medical.

Target Market(s)

Industry/Entity Type

Business Consultant

Contact Information for Business Card

Logo, Full Name, Title, Phone number, Email, company name, Address,

Font styles to use
Sans Serif

Requirements
Must have
• Tag line: Sharpening Focus for Truly Driven Performers
• Please use same colours as the logo.

```html
<!DOCTYPE html>
<html lang="en">
<head>
<meta charset="utf-8">
<title>KVOR Business Card</title>
<link rel="stylesheet" href="https://fonts.googleapis.com/css2?family=Open+Sans:wght@400;600;700;800&display=swap">
<style>
  :root {
    --teal: #00a9c5;
    --teal-deep: #0093ad;
    --ink: #3a3a3a;
    --muted: #666666;
    --card-white: #ffffff;
    --band-grey: #e4e7e8;
    --backdrop: #eeeeef;
  }
  * { box-sizing: border-box; margin: 0; padding: 0; }
  html, body {
    width: 1200px; height: 900px; overflow: hidden;
    background: var(--backdrop);
    font-family: "Open Sans", Arial, sans-serif;
  }
  .canvas { position: relative; width: 1200px; height: 900px; }
  .card {
    position: absolute; top: 300px;
    width: 525px; height: 300px;
    box-shadow: 0 6px 18px rgba(0,0,0,0.12);
    overflow: hidden;
  }
  /* Front face */
  .card-front { left: 50px; background: var(--card-white); }
  .holder { position: absolute; left: 34px; top: 30px; }
  .holder-name {
    color: var(--teal); font-weight: 700; font-size: 15px;
    letter-spacing: 0.5px; text-transform: uppercase;
  }
  .holder-title { color: var(--ink); font-size: 11.5px; margin-top: 2px; }
  .contact-list { position: absolute; left: 34px; top: 122px; list-style: none; }
  .contact-list li {
    display: flex; align-items: center; gap: 7px;
    color: var(--ink); font-size: 12px; line-height: 19px;
  }
  .contact-icon { width: 12px; height: 12px; flex: none; }
  .brand { position: absolute; text-align: left; }
  .card-front .brand { left: 262px; top: 118px; }
  .brand-row { display: flex; align-items: center; gap: 10px; }
  .brand-dot {
    width: 22px; height: 22px; border-radius: 50%; background: var(--teal);
  }
  .brand-name {
    color: var(--teal); font-weight: 800; font-size: 56px;
    line-height: 1; letter-spacing: 3px;
  }
  .brand-full {
    margin-top: 6px; padding-top: 5px;
    border-top: 1px solid currentColor;
    color: var(--teal); font-weight: 700; font-size: 10.5px;
    line-height: 1.25; text-transform: uppercase; letter-spacing: 0.3px;
    width: 200px;
  }
  .address {
    position: absolute; right: 34px; bottom: 30px; text-align: right;
    color: var(--ink); font-size: 12px; line-height: 18px;
    font-style: normal;
  }
  /* Back face */
  .card-back { left: 625px; background: var(--teal); }
  .card-back .brand { left: 150px; top: 78px; }
  .card-back .brand-name,
  .card-back .brand-full { color: var(--card-white); }
  .card-back .brand-dot { background: var(--card-white); }
  .card-back .brand-full { width: 225px; }
  .tagline-band {
    position: absolute; left: 0; right: 0; top: 228px; height: 36px;
    background: var(--band-grey);
    display: flex; align-items: center; justify-content: center;
    color: var(--teal); font-weight: 700; font-size: 12.5px;
    letter-spacing: 1px; text-transform: uppercase;
  }
</style>
</head>
<body>
<main class="canvas">
  <section class="card card-front" aria-label="Business card front">
    <div class="holder">
      <p class="holder-name">Marcus Hale</p>
      <p class="holder-title">Managing Director</p>
    </div>
    <ul class="contact-list">
      <li>
        <svg class="contact-icon" viewBox="0 0 24 24" aria-hidden="true"><path fill="#00a9c5" d="M6.6 10.8a15.1 15.1 0 0 0 6.6 6.6l2.2-2.2a1 1 0 0 1 1-.25 11.4 11.4 0 0 0 3.6.57 1 1 0 0 1 1 1V20a1 1 0 0 1-1 1A17 17 0 0 1 3 4a1 1 0 0 1 1-1h3.5a1 1 0 0 1 1 1c0 1.25.2 2.45.57 3.57a1 1 0 0 1-.25 1z"/></svg>
        (061)482 735 190
      </li>
      <li>
        <svg class="contact-icon" viewBox="0 0 24 24" aria-hidden="true"><rect x="2" y="5" width="20" height="14" rx="2" fill="#00a9c5"/><path d="M3 6l9 7 9-7" fill="none" stroke="#fff" stroke-width="1.8"/></svg>
        hello@kvormail.com
      </li>
      <li>
        <svg class="contact-icon" viewBox="0 0 24 24" aria-hidden="true"><circle cx="12" cy="12" r="10" fill="#00a9c5"/><path d="M2 12h20M12 2c3 3 3 17 0 20M12 2c-3 3-3 17 0 20" fill="none" stroke="#fff" stroke-width="1.4"/></svg>
        www.kvorlattice.com
      </li>
    </ul>
    <div class="brand">
      <div class="brand-row">
        <span class="brand-name">KVOR</span>
        <span class="brand-dot" aria-hidden="true"></span>
      </div>
      <p class="brand-full">Coherent Lattice of<br>Adaptive Reasoning Method</p>
    </div>
    <address class="address">
      88, Lattice Row,<br>Northvale, 40512
    </address>
  </section>

  <section class="card card-back" aria-label="Business card back">
    <div class="brand">
      <div class="brand-row">
        <span class="brand-name">KVOR</span>
        <span class="brand-dot" aria-hidden="true"></span>
      </div>
      <p class="brand-full">Coherent Lattice of<br>Adaptive Reasoning Method</p>
    </div>
    <p class="tagline-band">Sharpening Focus for Truly Driven Performers</p>
  </section>
</main>
</body>
</html>
```